QVR business card

Need a business card for a company that provides instructional design and elearning development services. The website is here: http://quorvane.studio/

I'm attaching a current logo, as well as the old business card design. While I like to keep it clean, the old design is too simplistic for my liking. The only idea I want to reuse from the old design is placing industry jargon on the back of the card, just need a better way to present it. But if you have other ideas for the back--feel free to experiment.

Please use the colors complementary to the color we have on the website. Thank you!

```html
<!DOCTYPE html>
<html lang="en">
<head>
<meta charset="utf-8">
<title>QVR business card</title>
<link rel="stylesheet" href="https://fonts.googleapis.com/css2?family=Arimo:wght@700&family=Varela+Round&display=swap">
<style>
  :root {
    --teal: #00b0ad;
    --gold: #c9b98a;
    --ink-grey: #5f6062;
    --paper: #ffffff;
    --backdrop: #e4e4e4;
  }
  * { margin: 0; padding: 0; box-sizing: border-box; }
  html, body { width: 1200px; height: 800px; overflow: hidden; }
  body {
    background: var(--backdrop);
    position: relative;
  }
  .card {
    position: absolute;
    top: 240px;
    width: 540px;
    height: 310px;
    border-radius: 18px;
    background: var(--paper);
    overflow: hidden;
    box-shadow: 0 4px 14px rgba(0,0,0,0.12);
  }
  /* Back of card: industry jargon */
  .card-back { left: 40px; padding: 46px 38px 0 40px; font-family: "Arimo", Arial, sans-serif; font-weight: 700; text-transform: uppercase; }
  .jargon { color: var(--ink-grey); font-size: 21px; line-height: 1.12; letter-spacing: 0.2px; }
  .headline { color: var(--teal); font-size: 47px; line-height: 1.15; margin: 10px 0 12px; letter-spacing: 0.5px; }
  /* Front of card */
  .card-front { left: 620px; font-family: "Varela Round", Arial, sans-serif; }
  .front-band { position: absolute; inset: 0; }
  .brand {
    position: absolute;
    left: 16px;
    top: 0;
    width: 120px;
    height: 310px;
    display: flex;
    align-items: center;
    justify-content: center;
  }
  .brand-lockup {
    transform: rotate(-90deg);
    display: flex;
    align-items: center;
    gap: 12px;
    white-space: nowrap;
  }
  .brand-mark { width: 22px; height: 22px; border-radius: 50%; background: var(--gold); }
  .brand-name { color: var(--gold); font-size: 34px; }
  .holder {
    position: absolute;
    left: 200px;
    top: 44px;
    color: var(--paper);
    font-size: 36px;
    letter-spacing: 0.5px;
  }
  .contact-list {
    position: absolute;
    left: 188px;
    top: 140px;
    list-style: none;
    color: var(--paper);
    font-size: 19px;
  }
  .contact-list li { display: flex; align-items: center; gap: 14px; height: 40px; }
  .contact-list svg { width: 22px; height: 22px; flex: none; }
</style>
</head>
<body>

<section class="card card-back" aria-label="Card back">
  <p class="jargon">Mobile learning SCORM instructional<br>design LMS MOOCs eLearning HTML5</p>
  <h2 class="headline">How can we help?</h2>
  <p class="jargon">Adult learning theory gamification<br>classroom xAPI blended learning</p>
</section>

<section class="card card-front" aria-label="Card front">
  <svg class="front-band" viewBox="0 0 540 310" preserveAspectRatio="none" aria-hidden="true">
    <polygon fill="var(--teal)" points="180,0 540,0 540,310 150,310 160,270 140,262 162,236 150,198 170,170 148,150 176,120 158,92 184,66 166,40"/>
  </svg>

  <div class="brand">
    <div class="brand-lockup">
      <span class="brand-mark"></span>
      <span class="brand-name">Quorvane</span>
    </div>
  </div>

  <h1 class="holder">Marten Oskarsen</h1>

  <ul class="contact-list">
    <li>
      <svg viewBox="0 0 24 24" aria-hidden="true"><path fill="#fff" d="M6.6 10.8c1.4 2.8 3.8 5.1 6.6 6.6l2.2-2.2c.3-.3.7-.4 1-.2 1.1.4 2.3.6 3.6.6.6 0 1 .4 1 1V20c0 .6-.4 1-1 1C10.6 21 3 13.4 3 4c0-.6.4-1 1-1h3.5c.6 0 1 .4 1 1 0 1.3.2 2.5.6 3.6.1.3 0 .7-.2 1z"/></svg>
      <span>555-014-2731</span>
    </li>
    <li>
      <svg viewBox="0 0 24 24" aria-hidden="true"><rect x="2" y="5" width="20" height="14" fill="none" stroke="#fff" stroke-width="2"/><path d="M2 5l10 8 10-8" fill="none" stroke="#fff" stroke-width="2"/></svg>
      <span>moskarsen@quorvane.studio</span>
    </li>
    <li>
      <svg viewBox="0 0 24 24" aria-hidden="true"><rect x="2" y="3" width="20" height="13" rx="1" fill="none" stroke="#fff" stroke-width="2"/><path d="M8 21h8M12 16v5" stroke="#fff" stroke-width="2"/></svg>
      <span>www.Quorvane.Studio</span>
    </li>
  </ul>
</section>

</body>
</html>
```